Agrarhandel benötigt Homepage
Zielgruppe
Wir sind ein Agrarhandel mit einem Warenumschlagslager im Sinne eines klassischen Einzelhandels und vertreiben Produkte an Landwirte.
Wir vertreiben folgende Hauptproduktgruppen:
Einzelfuttermittel
wie z.B. Sojaexktraktionsschrot. Die einzelnen Produkte könnten z.B. wie die Futtermittel auf folgender Seite dargestellt werden (https://www.kornprobe-beispiel.eu/de/produkt/trelomixan)
Mischfuttermittel
Hier bieten wir unseren Kunden an, individuelles Mischfutter auf Basis unserer Einzelfuttermittel herzustellen.
Weitere Details und weitere Produktbereiche habe ich in einer Powerpoint-Übersicht dargestellt.
Neben diesen Produkten wollen wir uns als Familienunternehmen selbst vorstellen. Zudem betreiben wir in unserer Familie zusätzlich einen Milchviehbetrieb den wir ebenfalls hervorheben möchten, da wir unseren Kunden gegenüber einerseits als Zulieferer aber auch als Kollege auftreten wollen.
Einzelfuttermittel: Hier können wir durch unsere Unabhängigkeit punkten, da wir nicht abhängig von bestimmten Lieferanten sind und dementsprechend unabhängig beraten können. Wir untersuchen im Vergleich zu unseren Wettbewerben die Qualität der Futtermittel bis ins Detail und können daher eine Transparenz bieten, die Konkurrenten in der Regel nicht bieten können. Unser Warenumschlagsplatz mit moderner Technik ermöglicht es uns äußerst kosteneffizient die Waren umschlagen und ausliefern zu können.
Mischfuttermittel: Auf Basis der vorhandenen Einzelfuttermittel stellen wir je nach Kundenwunsch individuelle Mischfutter her. Wir arbeiten mit offenen Deklarationen, sodass unsere Kunden jederzeit nachvollziehen können, ob auch die Einzelfuttermittel verwendet wurden, die sie bestellt haben und keine billigen Ersatzprodukte verwendet wurden.
Zudem sind wir BT und HUPA zertifiziert. Die aktuellen für unser Unternehmen ausgestellten Zertifikate müssen für unsere Kunden als Download zur Verfügung stehen. Statt dem HUPA-Logo bitte das ..
Aufgabenstellung
Wir möchten gerne ein zeitgemäße Homepage, jedoch muss auch berücksichtigt werden, dass unsere Kunden eher konservativ denken.

```html
<!DOCTYPE html>
<html lang="de">
<head>
<meta charset="utf-8">
<title>Talgrund Landhandel – Agrikultural Service</title>
<link href="https://fonts.googleapis.com/css2?family=Roboto:wght@400;500;700;900&display=swap" rel="stylesheet">
<style>
  :root {
    --yellow: #f6cf22;
    --yellow-soft: #f8dc5a;
    --green: #8cc63f;
    --ink: #1d1d1b;
    --muted: #555;
    --line: #e2e2e2;
    --paper: #ffffff;
    --dark-band: #2b2118;
  }
  * { box-sizing: border-box; margin: 0; padding: 0; }
  html, body { width: 1200px; height: 800px; overflow: hidden; }
  body { font-family: "Roboto", Arial, sans-serif; color: var(--ink); background: var(--paper); position: relative; }

  .site-header { height: 64px; display: flex; align-items: center; padding: 0 36px; border-bottom: 1px solid var(--line); }
  .brand { display: flex; align-items: center; gap: 8px; font-weight: 700; font-size: 20px; }
  .brand-dot { width: 14px; height: 14px; border-radius: 50%; background: var(--green); }
  .main-nav { display: flex; gap: 22px; margin-left: auto; font-size: 12px; font-weight: 700; align-items: center; }
  .main-nav .active { border-bottom: 2px solid var(--ink); padding-bottom: 2px; }
  .phone { margin-left: 22px; font-size: 12px; font-weight: 700; display: flex; align-items: center; gap: 8px; }
  .btn-subscribe { margin-left: 20px; background: var(--green); color: #fff; font-size: 10px; font-weight: 500; line-height: 1.2; text-align: center; padding: 6px 14px; }

  .hero { position: relative; height: 318px; }
  .hero-intro { position: absolute; left: 36px; top: 26px; font-size: 11px; }
  .hero-title { position: absolute; left: 36px; top: 44px; font-size: 44px; font-weight: 900; letter-spacing: -0.5px; }
  .hero-title .accent { color: var(--yellow); }
  .hero-news { position: absolute; right: 70px; top: 24px; width: 300px; font-size: 11px; line-height: 1.35; }
  .tiles { position: absolute; left: 36px; right: 36px; top: 112px; height: 192px; display: grid; grid-template-columns: repeat(4, 1fr); gap: 0; }
  .tile { position: relative; overflow: hidden; }
  .tile .photo { position: absolute; inset: 0; }
  .tile-label { position: absolute; left: 18px; bottom: 16px; color: #fff; font-weight: 700; font-size: 16px; line-height: 1.15; }
  .tile:nth-child(1) .photo { background: linear-gradient(180deg, #d9c8a9 0%, #8e9a52 55%, #4f7a26 100%); }
  .tile:nth-child(2) .photo { background: linear-gradient(180deg, #b8c6cc 0%, #6c5a46 60%, #3e3a33 100%); }
  .tile:nth-child(3) .photo { background: linear-gradient(180deg, #cfdbe4 0%, #c9b27a 45%, #8d7a4f 100%); }
  .tile:nth-child(4) .photo { background: linear-gradient(180deg, #b9ccde 0%, #a5a9ad 55%, #5b6064 100%); }

  .side-tab { position: absolute; right: 0; top: 150px; width: 30px; background: var(--yellow); display: flex; flex-direction: column; align-items: center; gap: 14px; padding: 12px 0; }

  .feed { position: relative; height: 232px; }
  .feed-field { position: absolute; left: 36px; top: 10px; width: 150px; height: 190px; background: linear-gradient(160deg, #6f8f3c 0%, #c7ae78 60%, #d8c096 100%); }
  .feed-grain { position: absolute; left: 150px; top: 0; width: 240px; height: 212px; background: linear-gradient(150deg, #7a5530 0%, #c99a62 55%, #e2c69a 100%); }
  .partner { position: absolute; left: 60px; top: 206px; font-weight: 700; font-size: 16px; color: #d4202c; display: flex; align-items: center; gap: 6px; }
  .feed-copy { position: absolute; left: 440px; top: 4px; width: 420px; }
  .eyebrow { font-size: 11px; color: var(--muted); }
  .feed-copy h2 { font-size: 26px; font-weight: 700; line-height: 1.15; margin-top: 4px; }
  .feed-copy p { font-size: 12px; color: var(--muted); margin-top: 8px; line-height: 1.4; }
  .checklist { list-style: none; margin-top: 10px; font-size: 12px; }
  .checklist li { display: flex; align-items: center; gap: 8px; margin-bottom: 6px; }
  .btn-contact { display: inline-block; margin-top: 6px; background: var(--yellow-soft); color: #fff; font-size: 12px; font-weight: 500; padding: 10px 22px; }
  .pellets { position: absolute; left: 880px; top: 60px; width: 180px; height: 90px; border-radius: 50% 50% 40% 40%; background: radial-gradient(ellipse at 50% 40%, #b39a74 0%, #8c7454 60%, #6e5a40 100%); }
  .to-top { position: absolute; right: 60px; top: 140px; width: 28px; height: 28px; border-radius: 50%; background: var(--yellow); display: flex; align-items: center; justify-content: center; }

  .fields { position: absolute; left: 0; right: 0; top: 614px; bottom: 0; background: linear-gradient(90deg, #3a2c1f 0%, #5b4431 45%, #7b5f45 100%); color: #fff; }
  .fields-title { position: absolute; left: 76px; top: 18px; font-size: 24px; font-weight: 700; }
  .fields-title::after { content: ""; position: absolute; left: 0; top: 40px; width: 320px; height: 1px; background: var(--yellow); }
  .tabs { position: absolute; left: 76px; top: 74px; width: 170px; list-style: none; font-size: 11px; }
  .tabs li { border: 1px solid rgba(255,255,255,0.35); padding: 6px 10px; margin-bottom: 5px; }
  .tabs li.active { background: var(--yellow); border-color: var(--yellow); color: var(--ink); }
  .tab-panel { position: absolute; left: 290px; top: 70px; width: 460px; }
  .tab-panel h3 { font-size: 14px; font-weight: 700; }
  .tab-panel p { font-size: 11px; margin-top: 6px; }
  .boxes { list-style: none; margin-top: 10px; display: grid; grid-template-columns: 1fr 1fr; gap: 8px 20px; font-size: 11px; }
  .boxes li { display: flex; align-items: center; gap: 8px; }
  .box { width: 18px; height: 18px; background: var(--yellow); display: flex; align-items: center; justify-content: center; }
</style>
</head>
<body>
  <header class="site-header">
    <div class="brand"><span class="brand-dot"></span>Talgrund Landhandel</div>
    <nav class="main-nav">
      <span class="active">Start</span><span>Aktuelles</span><span>Unternehmen</span><span>Sortiment</span><span>Shop</span><span>Kontakt</span>
      <svg width="14" height="14" viewBox="0 0 14 14" fill="none" stroke="#1d1d1b" stroke-width="1.6"><circle cx="6" cy="6" r="4.5"/><line x1="9.5" y1="9.5" x2="13" y2="13"/></svg>
    </nav>
    <div class="phone">+49 9000 555120</div>
    <div class="btn-subscribe">Jetzt<br>Abonnieren</div>
  </header>

  <section class="hero">
    <p class="hero-intro">Herzlich Willkommen bei Talgrund Landhandel, Ihrem Experten in der Agrarwirtschaft.</p>
    <h1 class="hero-title"><span class="accent">Agrikultural</span> Service</h1>
    <p class="hero-news">Jetzt neu! Abonnieren Sie unsere Newsletter und profitieren Sie als erster von aktuellen Informationen!</p>
    <div class="tiles">
      <div class="tile"><div class="photo" role="img" aria-label="Traktor beim Spritzen auf einem grünen Feld"></div><span class="tile-label">Agrarwirtschaft</span></div>
      <div class="tile"><div class="photo" role="img" aria-label="Landwirte vor einem Traktor"></div><span class="tile-label">Landwirtschaftliche<br>Bedarf</span></div>
      <div class="tile"><div class="photo" role="img" aria-label="Mähdrescher im Getreidefeld"></div><span class="tile-label">Getreide</span></div>
      <div class="tile"><div class="photo" role="img" aria-label="Futtersilos unter blauem Himmel"></div><span class="tile-label">Futter</span></div>
    </div>
  </section>

  <aside class="side-tab" aria-label="Schnellzugriff">
    <svg width="14" height="14" viewBox="0 0 14 14" fill="none" stroke="#fff" stroke-width="1.3"><path d="M1 2h2l2 7h7l1-5H4"/><circle cx="6" cy="12" r="1"/><circle cx="11" cy="12" r="1"/></svg>
    <svg width="14" height="14" viewBox="0 0 14 14" fill="none" stroke="#fff" stroke-width="1.3"><rect x="1.5" y="2.5" width="11" height="9"/><line x1="1.5" y1="6" x2="12.5" y2="6"/></svg>
    <svg width="14" height="14" viewBox="0 0 14 14" fill="none" stroke="#fff" stroke-width="1.3"><rect x="1.5" y="3.5" width="11" height="8"/><line x1="1.5" y1="6.5" x2="12.5" y2="6.5"/></svg>
  </aside>

  <section class="feed">
    <div class="feed-field" role="img" aria-label="Luftaufnahme von Feldern"></div>
    <div class="feed-grain" role="img" aria-label="Hand mit Getreidekörnern"></div>
    <div class="partner">Kornado</div>
    <div class="feed-copy">
      <span class="eyebrow">Futter</span>
      <h2>Für die Optimalste<br>Aufzucht Ihre Tiere</h2>
      <p>Hier finden Sie direkt den richtigen Ansprechpartner<br>für die Produkte, die Sie interessieren.</p>
      <ul class="checklist">
        <li><svg width="10" height="10" viewBox="0 0 10 10" fill="none" stroke="#f6cf22" stroke-width="1.8"><path d="M1 5l3 3 5-7"/></svg>Handel</li>
        <li><svg width="10" height="10" viewBox="0 0 10 10" fill="none" stroke="#f6cf22" stroke-width="1.8"><path d="M1 5l3 3 5-7"/></svg>Transport</li>
        <li><svg width="10" height="10" viewBox="0 0 10 10" fill="none" stroke="#f6cf22" stroke-width="1.8"><path d="M1 5l3 3 5-7"/></svg>Agrarwirtschaft</li>
      </ul>
      <span class="btn-contact">Ansprechpartner</span>
    </div>
    <div class="pellets" role="img" aria-label="Haufen Futterpellets"></div>
    <div class="to-top"><svg width="12" height="12" viewBox="0 0 12 12" fill="none" stroke="#fff" stroke-width="1.5"><path d="M6 11V1M2 5l4-4 4 4"/></svg></div>
  </section>

  <section class="fields" role="img" aria-label="Milchkühe im Stall, abgedunkelt als Hintergrund">
    <h2 class="fields-title">Tätigkeitsfelder</h2>
    <ul class="tabs">
      <li class="active">› Futter</li>
      <li>Getreide</li>
      <li>Saatgut</li>
      <li>Landwirtschaftlicher Bedarf</li>
    </ul>
    <div class="tab-panel">
      <h3>Futter</h3>
      <p>Wir bieten Ihnen Futtermittel für sowohl Nutz- als auch Hobbytiere!</p>
      <ul class="boxes">
        <li><span class="box"><svg width="10" height="10" viewBox="0 0 10 10" fill="none" stroke="#fff" stroke-width="1.8"><path d="M1 5l3 3 5-7"/></svg></span>Milchvieh</li>
        <li><span class="box"><svg width="10" height="10" viewBox="0 0 10 10" fill="none" stroke="#fff" stroke-width="1.8"><path d="M1 5l3 3 5-7"/></svg></span>Schweine</li>
        <li><span class="box"><svg width="10" height="10" viewBox="0 0 10 10" fill="none" stroke="#fff" stroke-width="1.8"><path d="M1 5l3 3 5-7"/></svg></span>Hühner</li>
        <li><span class="box"><svg width="10" height="10" viewBox="0 0 10 10" fill="none" stroke="#fff" stroke-width="1.8"><path d="M1 5l3 3 5-7"/></svg></span>Biofutter</li>
        <li><span class="box"><svg width="10" height="10" viewBox="0 0 10 10" fill="none" stroke="#fff" stroke-width="1.8"><path d="M1 5l3 3 5-7"/></svg></span>Kleintierfutter</li>
      </ul>
    </div>
  </section>
</body>
</html>
```